Heron Loan Partners Business Card

We need a business card design for our mortgage servicing company. In addition to servicing the loans of homeowners, we help homeowners with purchasing their homes and any mortgage refinancing. We would like to see designs that use the colors in the logo attached below (gold-ish yellow and navy blue), and any other design you deem fit! The design should communicate a simpler life with smart mortgages provided by Heron.

```html
<!DOCTYPE html>
<html lang="en">
<head>
<meta charset="utf-8">
<title>Heron Loan Partners Business Card</title>
<link rel="stylesheet" href="https://fonts.googleapis.com/css2?family=Poppins:wght@400;500;600&family=Libre+Baskerville:wght@700&display=swap">
<style>
  :root {
    --navy: #241f58;
    --navy-light: #2f3a8c;
    --gold: #e1ab2a;
    --white: #ffffff;
    --stage: #cfcfcf;
  }
  * { margin: 0; padding: 0; box-sizing: border-box; }
  html, body { width: 1200px; height: 800px; overflow: hidden; }
  body {
    background: var(--stage);
    display: flex;
    align-items: center;
    justify-content: center;
    gap: 40px;
    font-family: "Poppins", sans-serif;
  }
  .card {
    width: 560px;
    height: 320px;
    border: 2px solid var(--gold);
    position: relative;
    overflow: hidden;
  }
  /* Front */
  .card-front { background: var(--white); }
  .brand-area {
    height: 42%;
    display: flex;
    align-items: center;
    justify-content: center;
  }
  .brand-name {
    font-family: "Poppins", sans-serif;
    font-weight: 600;
    font-size: 30px;
    color: var(--gold);
    letter-spacing: 0.5px;
  }
  .info-band {
    position: absolute;
    left: 0; right: 0; bottom: 0;
    height: 58%;
    background: var(--navy);
    border-top: 2px solid var(--gold);
    padding: 30px 34px 0;
    color: var(--white);
  }
  .info-row { display: flex; align-items: center; }
  .person { width: 215px; }
  .person-name {
    font-family: "Libre Baskerville", serif;
    font-weight: 700;
    font-size: 20px;
    color: var(--gold);
    line-height: 1.2;
  }
  .person-role { font-size: 15px; font-weight: 400; }
  .divider {
    width: 2px;
    height: 70px;
    background: var(--gold);
    margin: 0 20px 0 0;
  }
  .contacts { list-style: none; font-size: 14px; line-height: 1.6; }
  .contacts li { display: flex; align-items: center; gap: 8px; }
  .contacts svg { width: 13px; height: 13px; flex: none; }
  .address { margin-top: 22px; font-size: 15px; letter-spacing: 0.2px; }
  /* Back */
  .card-back { background: var(--navy); }
  .back-texture {
    position: absolute; inset: 0;
    background: linear-gradient(135deg, var(--navy) 20%, #2a2d75 60%, var(--navy-light) 100%);
    opacity: 0.75;
  }
  .back-brand {
    position: absolute;
    left: 50%; top: 62%;
    transform: translate(-50%, -50%);
    font-weight: 600;
    font-size: 24px;
    color: var(--gold);
    white-space: nowrap;
  }
</style>
</head>
<body>
  <section class="card card-front" aria-label="Card front">
    <div class="brand-area">
      <span class="brand-name">Heron Loan Partners</span>
    </div>
    <div class="info-band">
      <div class="info-row">
        <div class="person">
          <p class="person-name">Daniel Reyes</p>
          <p class="person-role">Managing Director</p>
        </div>
        <div class="divider"></div>
        <ul class="contacts">
          <li>
            <svg viewBox="0 0 24 24" aria-hidden="true"><path fill="var(--gold)" d="M6.6 10.8a15.1 15.1 0 0 0 6.6 6.6l2.2-2.2a1 1 0 0 1 1-.25 11.4 11.4 0 0 0 3.6.57 1 1 0 0 1 1 1V20a1 1 0 0 1-1 1A17 17 0 0 1 3 4a1 1 0 0 1 1-1h3.5a1 1 0 0 1 1 1c0 1.25.2 2.45.57 3.57a1 1 0 0 1-.25 1z"/></svg>
            044-987 654 321
          </li>
          <li>
            <svg viewBox="0 0 24 24" aria-hidden="true"><path fill="var(--gold)" d="M2 5h20v14H2z"/><path fill="none" stroke="var(--navy)" stroke-width="2" d="M2 5l10 8 10-8"/></svg>
            info@heronloan.com
          </li>
          <li>
            <svg viewBox="0 0 24 24" aria-hidden="true"><circle cx="12" cy="12" r="10" fill="var(--gold)"/><path fill="none" stroke="var(--navy)" stroke-width="1.5" d="M2 12h20M12 2c3 3 3 17 0 20M12 2c-3 3-3 17 0 20"/></svg>
            www.heronloanpartners.com
          </li>
        </ul>
      </div>
      <p class="address">88, Harbor View Road 30418, Country Name</p>
    </div>
  </section>

  <section class="card card-back" aria-label="Card back">
    <div class="back-texture" role="img" aria-label="Tone-on-tone repeating brand pattern in navy and blue"></div>
    <span class="back-brand">Heron Loan Partners</span>
  </section>
</body>
</html>
```